Velborix advertisement one page flyer design

We need a flyer design for our company to advertise what we offer, it only needs to be one sided, approx A5 in size.
Our logo: http://velborix-example.com/images/logo.png (I will provide in high-res later)
We offer, website design, development, bespoke applications. We would like to advertise that we can be hired for short term contracts for companies who need help with their work load.
Some of, but not limited to the systems we build are content management systems, e-commerce systems & event booking systems.
Our strap line is "We design, develop and deliver", a nice sleek redesign of the image on our website would be nice, but not required 100% - http://velborix-example.com/
Other details to put on the flyer:-
Email: hello@velborix-example.com
Tel: 01632 960 417
Address: Velborix Ltd, Crest Suites, Dunmoor Road, Cheltenham, GL53 4QT
We welcome any other ideas.

```html
<!DOCTYPE html>
<html lang="en">
<head>
<meta charset="utf-8">
<title>Velborix flyer</title>
<link rel="stylesheet" href="https://fonts.googleapis.com/css2?family=Open+Sans:wght@700;800&family=Short+Stack&family=Roboto+Condensed:wght@700&family=Russo+One&family=Arimo:wght@400;700&display=swap">
<style>
  :root {
    --orange: #e8761c;
    --orange-deep: #b5460b;
    --orange-dark: #7a2a06;
    --orange-glow: #f6a34a;
    --grey-dark: #5d5b5c;
    --grey-mid: #c3c3c3;
    --grey-light: #e3e3e3;
    --white: #ffffff;
    --ink: #222222;
    --page: #efefef;
  }
  * { margin: 0; padding: 0; box-sizing: border-box; }
  html, body { width: 862px; height: 1200px; overflow: hidden; background: var(--page); }
  .flyer {
    position: absolute; left: 35px; top: 39px;
    width: 792px; height: 1122px; overflow: hidden;
    background: var(--grey-light);
    font-family: "Open Sans", Arial, sans-serif;
  }
  .flyer-shapes { position: absolute; inset: 0; }
  .hero-visual {
    position: absolute; left: 0; top: 0; width: 792px; height: 560px;
    background:
      radial-gradient(ellipse 55% 50% at 68% 38%, var(--orange-glow) 0%, rgba(232,118,28,0.6) 45%, transparent 75%),
      linear-gradient(135deg, var(--orange-dark) 0%, var(--orange-deep) 45%, var(--orange) 100%);
  }
  .brand-name {
    position: absolute; left: 30px; top: 82px;
    font-size: 64px; font-weight: 800; color: var(--white); letter-spacing: -1px;
  }
  .intro {
    position: absolute; left: 28px; top: 186px;
    color: var(--white); font-size: 23px; font-weight: 700; line-height: 34px;
  }
  .intro p + p { margin-top: 34px; }
  .section-title {
    position: absolute; font-family: "Short Stack", cursive;
    color: var(--grey-dark); font-weight: 400; white-space: nowrap;
  }
  .how-title { left: 30px; top: 580px; font-size: 33px; }
  .solutions-title { left: 482px; top: 578px; font-size: 24px; color: var(--ink); }
  .strapline {
    position: absolute; left: 50px; font-family: "Russo One", sans-serif;
    color: var(--grey-dark); font-size: 74px; line-height: 1; letter-spacing: 1px; white-space: nowrap;
  }
  .strapline small { font-size: 40px; margin-right: 10px; }
  .strap-design { top: 655px; }
  .strap-develop { top: 788px; }
  .strap-deliver { top: 920px; }
  .services { position: absolute; left: 482px; top: 630px; list-style: none; }
  .service {
    display: flex; align-items: center; height: 57.5px; white-space: nowrap;
    font-family: "Roboto Condensed", sans-serif; font-weight: 700; font-size: 20px; color: var(--ink);
  }
  .service svg { width: 52px; height: 52px; margin-right: 10px; flex: none; }
  .contact-cta {
    position: absolute; left: 27px; top: 1055px; white-space: nowrap;
    color: var(--orange); font-size: 27px; font-weight: 700;
  }
  .contact-details {
    position: absolute; left: 372px; top: 1012px; width: 412px;
    font-family: "Arimo", Arial, sans-serif; font-style: normal;
    font-size: 17px; color: var(--ink); line-height: 25px; white-space: nowrap;
  }
  .contact-row { display: flex; align-items: flex-start; }
  .contact-row svg { flex: none; margin-right: 10px; margin-top: 3px; }
  .contact-row + .contact-row { margin-top: 14px; align-items: center; }
  .contact-row + .contact-row svg { margin-top: 0; }
  .contact-phone { font-weight: 700; margin-right: 12px; }
  .contact-row .mail-icon { margin-right: 6px; }
</style>
</head>
<body>
<main class="flyer">
  <div class="hero-visual" role="img" aria-label="Photo of a hand touching glowing orange web tiles"></div>

  <svg class="flyer-shapes" viewBox="0 0 792 1122" aria-hidden="true">
    <path d="M0 520 C 200 470, 420 560, 560 530 C 660 510, 740 460, 792 420 L792 1122 L0 1122 Z" fill="var(--orange)"/>
    <path d="M0 545 C 200 500, 420 585, 570 555 C 670 535, 745 490, 792 455 L792 1122 L0 1122 Z" fill="var(--grey-light)"/>
    <path d="M0 540 C 200 490, 420 575, 570 545 C 670 525, 745 480, 792 445 L792 470 C 745 505, 670 555, 570 572 C 420 600, 200 520, 0 580 Z" fill="var(--grey-dark)"/>
    <path d="M0 580 C 200 520, 380 595, 455 575 L455 972 L345 1028 L0 1028 Z" fill="var(--orange)"/>
    <path d="M345 1028 L455 972 L792 985 L792 1122 L345 1122 Z" fill="var(--grey-mid)"/>
  </svg>

  <div class="brand-name">Velborix</div>

  <div class="intro">
    <p>We offer,<br>website design, development,<br>bespoke application</p>
    <p>we can be hired for short term<br>contract for. companies<br>who need help with<br>then work load</p>
  </div>

  <h2 class="section-title how-title">How It Works?</h2>
  <div class="strapline strap-design"><small>we</small>design</div>
  <div class="strapline strap-develop"><small>we</small>devlop</div>
  <div class="strapline strap-deliver"><small>we</small>deliver</div>

  <h2 class="section-title solutions-title">Solutions We Provide</h2>
  <ul class="services">
    <li class="service"><svg viewBox="0 0 52 52"><circle cx="26" cy="26" r="25" fill="var(--orange)"/><rect x="17" y="14" width="18" height="24" fill="none" stroke="#fff" stroke-width="2.5"/><path d="M21 21h10M21 26h10M21 31h7" stroke="#fff" stroke-width="2"/></svg>Content Management</li>
    <li class="service"><svg viewBox="0 0 52 52"><circle cx="26" cy="26" r="25" fill="var(--orange)"/><circle cx="26" cy="26" r="12" fill="none" stroke="#fff" stroke-width="2.5"/><path d="M14 26h24M26 14v24" stroke="#fff" stroke-width="2"/></svg>Web Design</li>
    <li class="service"><svg viewBox="0 0 52 52"><circle cx="26" cy="26" r="25" fill="var(--orange)"/><circle cx="26" cy="26" r="11" fill="none" stroke="#fff" stroke-width="2.5"/></svg>Bespoke System</li>
    <li class="service"><svg viewBox="0 0 52 52"><circle cx="26" cy="26" r="25" fill="var(--orange)"/><circle cx="24" cy="25" r="11" fill="none" stroke="#fff" stroke-width="2.5"/><rect x="30" y="30" width="10" height="7" fill="#fff"/></svg>e-commerce</li>
    <li class="service"><svg viewBox="0 0 52 52"><circle cx="26" cy="26" r="25" fill="var(--orange)"/><rect x="15" y="20" width="18" height="18" fill="none" stroke="#fff" stroke-width="2.5"/><path d="M24 29l12-14" stroke="#fff" stroke-width="3"/></svg>Subscription System</li>
    <li class="service"><svg viewBox="0 0 52 52"><circle cx="26" cy="26" r="25" fill="var(--orange)"/><rect x="15" y="24" width="22" height="6" fill="#fff"/><rect x="15" y="32" width="22" height="6" fill="#fff"/><path d="M18 14l8 7 8-7" fill="none" stroke="#fff" stroke-width="2.5"/></svg>Domain &amp; Hosting</li>
  </ul>

  <div class="contact-cta">Get In Tuch Today</div>

  <address class="contact-details">
    <div class="contact-row">
      <svg width="14" height="20" viewBox="0 0 14 20"><path d="M7 0a7 7 0 0 0-7 7c0 5 7 13 7 13s7-8 7-13a7 7 0 0 0-7-7z" fill="var(--ink)"/><circle cx="7" cy="7" r="2.5" fill="var(--grey-mid)"/></svg>
      <span>Velborix Ltd, Crest Suites,<br>Dunmoor Road, Cheltenham, GL53 4QT</span>
    </div>
    <div class="contact-row">
      <svg width="16" height="22" viewBox="0 0 16 22"><path d="M4 1l4 5-2 3c1 3 3 6 5 7l3-2 2 4-4 3C6 19 1 11 2 3z" fill="none" stroke="var(--ink)" stroke-width="1.8"/></svg>
      <span class="contact-phone">01632 960 417</span>
      <svg class="mail-icon" width="18" height="13" viewBox="0 0 18 13"><rect x="0" y="0" width="18" height="13" fill="var(--ink)"/><path d="M0 0l9 7 9-7" fill="none" stroke="var(--grey-mid)" stroke-width="1.5"/></svg>
      <span>hello@velborix-example.com</span>
    </div>
  </address>
</main>
</body>
</html>
```